I would like a single page website for Skyward Rentals Pacific. In the file list provided there is basic information to be included as well as our logo with colors, fonts and images to be included.
Site must be very simple and be able to be loaded onto smart phones etc very quickly.
Site needs to be very smart in appearance

Target Market(s)

All prospective drone customers from Police to Parties.

Industry/Entity Type

Hire

Requirements
Must have
• Must have variation of color schemes supplied
Nice to have
• Must be very eye catching without going over the top
Should not have
• Anything slow to load.

```html
<!DOCTYPE html>
<html lang="en">
<head>
<meta charset="utf-8">
<title>Skyward Rentals Pacific</title>
<link href="https://fonts.googleapis.com/css2?family=Open+Sans:wght@400;600;700&family=Oswald:wght@400;600&display=swap" rel="stylesheet">
<style>
:root{
  --green:#7cc242;
  --green-dark:#5ea52c;
  --ink:#2b2b2b;
  --text:#555;
  --dark:#2e2e2e;
  --nav:#3a3a3a;
  --light:#f2f2f2;
  --white:#fff;
}
*{margin:0;padding:0;box-sizing:border-box}
html,body{width:720px;height:1200px;overflow:hidden;background:var(--white)}
body{font-family:"Open Sans",Arial,sans-serif;color:var(--text);font-size:10px}
.page{width:720px;height:1200px;position:relative}
.header{height:62px;display:flex;align-items:center;justify-content:space-between;padding:0 34px}
.brand{display:flex;align-items:center;gap:8px;font-family:"Oswald",Arial,sans-serif;font-weight:600;font-size:20px;color:var(--green);text-transform:uppercase;line-height:1}
.brand-dot{width:16px;height:16px;border-radius:50%;background:var(--green)}
.header-actions{display:flex;gap:8px}
.btn{display:inline-block;background:var(--green);color:var(--white);font-size:9px;font-weight:700;padding:6px 10px;text-transform:uppercase;letter-spacing:.3px}
.nav{height:20px;background:var(--nav);display:flex;justify-content:center;gap:34px;align-items:center}
.nav a{color:#ddd;font-size:8px;font-weight:600;text-transform:uppercase;text-decoration:none}
.nav a.active{color:var(--white);background:var(--green);padding:5px 9px}
.hero{position:relative;height:350px;background:linear-gradient(180deg,#5c6a4f 0%,#8a8c7e 45%,#6d6a60 100%)}
.hero-caption{position:absolute;left:360px;top:150px;width:300px;color:var(--white)}
.hero-caption h2{font-family:"Oswald",Arial,sans-serif;font-weight:600;font-size:17px;line-height:1.3;text-transform:uppercase;margin-bottom:10px}
.hero-caption p{font-size:9px;line-height:1.5;margin-bottom:10px;color:#eee}
.welcome{display:flex;gap:24px;padding:20px 34px 0;height:240px}
.welcome-text{width:330px}
h3.section-title{font-family:"Oswald",Arial,sans-serif;font-weight:400;font-size:20px;color:var(--ink);margin-bottom:8px}
.lead{color:var(--green-dark);font-size:8.5px;line-height:1.5;margin-bottom:10px}
.services{list-style:none;margin-bottom:12px}
.services li{font-size:8px;line-height:1.55;color:var(--ink);padding-left:12px;position:relative}
.services li::before{content:"";position:absolute;left:0;top:4px;width:4px;height:4px;background:var(--green);border-radius:50%}
.video{width:300px;height:150px;margin-top:50px;background:linear-gradient(180deg,#9ec3e0 0%,#b7cfa8 55%,#6f9a4c 100%);position:relative}
.video-bar{position:absolute;left:0;right:0;bottom:0;height:14px;background:rgba(0,0,0,.7)}
.play{position:absolute;left:50%;top:50%;transform:translate(-50%,-50%)}
.works{height:268px;background:linear-gradient(180deg,#3a3a3a,#262626);padding:26px 34px 0}
.works h3{text-align:center;color:var(--white);font-family:"Oswald",Arial,sans-serif;font-weight:400;font-size:20px;margin-bottom:20px}
.work-grid{display:flex;gap:14px}
.work{width:152px;background:var(--white)}
.work-img{height:118px}
.work-body{padding:6px 7px 8px}
.work-body h4{font-size:9.5px;font-weight:700;color:var(--ink);margin-bottom:2px}
.work-body span{font-size:8px;color:var(--green-dark)}
.info{display:flex;height:208px;background:var(--light);padding:20px 34px 0;gap:40px}
.why{width:326px}
.why-row{display:flex;gap:12px}
.why-img{width:120px;height:90px;background:linear-gradient(180deg,#eaeaea,#9a9a9a)}
.why-text p{font-size:8px;line-height:1.5;color:var(--ink);margin-bottom:8px}
.clients{flex:1}
.quote{background:var(--white);border:1px solid #ddd;padding:10px;font-size:8px;line-height:1.55;color:var(--text);position:relative}
.author{display:flex;justify-content:flex-end;align-items:center;gap:8px;margin-top:12px}
.author-photo{width:34px;height:34px;border-radius:50%;background:#c9c0b6}
.author b{display:block;font-size:8.5px;color:var(--ink)}
.author small{font-size:7.5px}
.footer{position:absolute;left:0;right:0;bottom:0;height:72px;background:var(--dark);display:flex;align-items:center;justify-content:space-between;padding:0 34px;color:#ccc;font-size:8px}
.social{display:flex;gap:6px}
.social span{width:18px;height:18px;border-radius:50%;background:#555;display:block}
</style>
</head>
<body>
<div class="page">
  <header class="header">
    <div class="brand"><span class="brand-dot"></span>Skyward Rentals Pacific</div>
    <div class="header-actions">
      <span class="btn">Call us: 0400 123 456</span>
      <span class="btn">Online Booking</span>
    </div>
  </header>
  <nav class="nav">
    <a class="active">Home</a><a>About us</a><a>Drone Services</a><a>Blog</a><a>Feedback</a><a>Videos</a><a>Photos</a><a>Contact us</a>
  </nav>
  <section class="hero" role="img" aria-label="Aerial photo of a white drone hovering above suburban buildings">
    <div class="hero-caption">
      <h2>Lorem ipsum is simply dummy text of the printing</h2>
      <p>Our certified pilots capture sharp aerial footage for events, inspections and surveys across the region, with fast booking and clear pricing on every job.</p>
      <span class="btn">Click for more detail</span>
    </div>
  </section>
  <section class="welcome">
    <div class="welcome-text">
      <h3 class="section-title">Welcome</h3>
      <p class="lead">CASA certified company and CASA endorsed pilot, with Full Public Liability Insurance. All operating licences are in place and we are certified on the operator.</p>
      <ul class="services">
        <li>Special Occasions, Childrens Birthday Parties, Weddings</li>
        <li>Sporting events Drill. Video of yourself participating in marathons etc</li>
        <li>Real Estate Brochures</li>
        <li>Construction project updates for remote stake holders</li>
        <li>Surveillance 3 Plans. Local council/owner/bank</li>
        <li>Building Roof Condition Inspections</li>
        <li>Lost pets</li>
        <li>Accident reconstructions</li>
        <li>Insurance assessing</li>
      </ul>
      <span class="btn">Click for more detail</span>
    </div>
    <div class="video" role="img" aria-label="Video still of a pilot flying a drone in a park">
      <svg class="play" width="40" height="28" viewBox="0 0 40 28"><rect width="40" height="28" rx="6" fill="#222" opacity=".85"/><path d="M16 8l10 6-10 6z" fill="#fff"/></svg>
      <div class="video-bar"></div>
    </div>
  </section>
  <section class="works">
    <h3>Recent Works</h3>
    <div class="work-grid">
      <article class="work"><div class="work-img" role="img" aria-label="Children at a birthday party" style="background:linear-gradient(180deg,#d9a65a,#b5553f)"></div><div class="work-body"><h4>Childrens Birthday Parties</h4><span>Read more &rsaquo;</span></div></article>
      <article class="work"><div class="work-img" role="img" aria-label="Aerial view of a sports stadium" style="background:linear-gradient(180deg,#8aa2c0,#4f8a3a)"></div><div class="work-body"><h4>Sporting Events</h4><span>Read more &rsaquo;</span></div></article>
      <article class="work"><div class="work-img" role="img" aria-label="Drone flying over a building site" style="background:linear-gradient(180deg,#b9cde0,#6e7060)"></div><div class="work-body"><h4>Building Condition Inspections</h4><span>Read more &rsaquo;</span></div></article>
      <article class="work"><div class="work-img" role="img" aria-label="Aerial view of a house and garden" style="background:linear-gradient(180deg,#6f9550,#9a7a5a)"></div><div class="work-body"><h4>Insurance Assessing</h4><span>Read more &rsaquo;</span></div></article>
    </div>
  </section>
  <section class="info">
    <div class="why">
      <h3 class="section-title">Why Choose us</h3>
      <div class="why-row">
        <div class="why-img" role="img" aria-label="White quadcopter drone"></div>
        <div class="why-text">
          <p>CASA certified company and CASA endorsed pilot, with Full Public Liability Insurance. All operating licences are in place and are carried on the operator.</p>
          <p>All drones are maintained in full CASA compliance standards.</p>
          <span class="btn">Click for more detail</span>
        </div>
      </div>
    </div>
    <div class="clients">
      <h3 class="section-title">What client say</h3>
      <div class="quote">Prime aerial shots delivered on time and within budget. The team was friendly, quick to reply and clearly knew their craft. We will book again for our next site.</div>
      <div class="author">
        <div><b>Dana Reyes</b><small>Manager of Industry</small></div>
        <div class="author-photo" role="img" aria-label="Client portrait"></div>
      </div>
    </div>
  </section>
  <footer class="footer">
    <span>&copy;2015. Skyward Rentals Pacific. All Rights Reserved. Terms &amp; Conditions Privacy Policy</span>
    <div class="social"><span></span><span></span><span></span><span></span><span></span><span></span><span></span></div>
  </footer>
</div>
</body>
</html>
```